Design website for new email startup

We are starting a company called Pingo.QZ (it will live at http://pingo.qz).

We would like the main landing page for our site designed. We have provided a very simple wireframe to help provide direction for the content it should include, but we do not expect the designers to adhere to it at all - we encourage unique ideas. There is some sample text in the wireframe - this does not have to be used, but may provide ideas.

We provide an easy way for people to manage email for a custom domain name. For example if you own "yourhouseword.example" you can point your DNS records to us and we'll make it easy to have emails addressed to your domain get forwarded to your existing email (gmail, etc). Folks running blogs, and other small sites can quickly setup email addresses for their domains and manage them in one place.

(For technical folks, we have you point your dns mx records to us, hence the name. That way all your email hits us and we can redirect it wherever you want. We make it easy to manage a single domain or a bunch of domains. Many domain registrars offer this service for a fee, and have clumsy management tools. We provide a robust simple toolset for free, as well as premium options).

The goal of the landing page is to get folks into the signup flow. The second priority flow is to have them take a look at the premium plan offerings.

We may offer the winning designer additional work for the remainder of the site design.
Updates

I've changed this project to a committed payment.  It is no longer refundable.  Thank you.

Target Market(s)

Bloggers, podcasters, designers, app developers - people who are a little tech savvy.

Industry/Entity Type

It Company

Font styles to use
Sans Serif

Colors

Designer to choose colors to be used in the design.

Requirements
Must have
• A full fidelity mockup (comp) of the landing page including the source file (psd, ai, etc).

Some sort of logo treatment for the pingo.qz brand

A call to action for signup, such as the suggested 'Get Started Here'
Nice to have
• A hip startup feel

Incorporation of the email theme

Give the impression it is simple, easy and fast

```html
<!DOCTYPE html>
<html lang="en">
<head>
<meta charset="utf-8">
<title>Pingo Qz – Email forwarding for your domain</title>
<link rel="stylesheet" href="https://fonts.googleapis.com/css2?family=Open+Sans:wght@400;600;700&display=swap">
<style>
  :root {
    --header-top: #2fa9e0;
    --header-bottom: #1787cf;
    --header-edge: #0f6fae;
    --slogan: #9fd8f5;
    --login-bg: #0b4f8c;
    --hero-dark: #3b4a55;
    --hero-mid: #5c6b75;
    --hero-light: #c9d2d6;
    --btn-blue-top: #2a9be0;
    --btn-blue-bottom: #0f6fbf;
    --btn-orange-top: #ff9a1a;
    --btn-orange-bottom: #f06d00;
    --link: #1c3f94;
    --body-text: #555b60;
    --card-border: #d8dadc;
    --page-bg: #f4f4f4;
    --footer-text: #444;
    --icon: #6d6d6d;
    --white: #ffffff;
  }
  * { box-sizing: border-box; margin: 0; padding: 0; }
  html, body {
    width: 1200px; height: 870px; overflow: hidden;
    font-family: "Open Sans", sans-serif;
    background: var(--page-bg);
  }
  .page { position: relative; width: 1200px; height: 870px;
    background: radial-gradient(ellipse at 50% 60%, #ffffff 0%, var(--page-bg) 75%); }

  .site-header {
    height: 105px;
    background: linear-gradient(var(--header-top), var(--header-bottom));
    border-bottom: 2px solid var(--header-edge);
  }
  .header-inner { position: relative; width: 1000px; margin: 0 auto; height: 100%; }
  .brand { position: absolute; left: 6px; top: 24px; color: var(--white); white-space: nowrap; }
  .brand-name { font-size: 36px; font-weight: 600; line-height: 1; letter-spacing: -0.3px; }
  .brand-slogan { font-size: 14px; color: var(--slogan); margin-top: 3px; }
  .main-nav { position: absolute; right: 36px; top: 44px; display: flex; align-items: center; gap: 35px; white-space: nowrap; }
  .main-nav a { color: var(--white); text-decoration: none; font-size: 16px; }
  .main-nav .login {
    background: var(--login-bg); border-radius: 3px; padding: 6px 19px; font-size: 15px;
    box-shadow: inset 0 1px 0 rgba(255,255,255,0.15);
  }

  .hero {
    position: relative; height: 472px; overflow: hidden;
    background: radial-gradient(ellipse at 68% 30%, var(--hero-light) 0%, var(--hero-mid) 40%, var(--hero-dark) 80%);
  }
  .hero-visual {
    position: absolute; left: 600px; top: 30px; width: 420px; height: 442px;
    background: radial-gradient(ellipse at 50% 40%, #f2f4f4 0%, #dfe4e4 35%, rgba(200,170,150,0.35) 70%, rgba(90,105,115,0) 100%);
  }
  .hero-copy { position: absolute; left: 106px; top: 136px; width: 540px; color: var(--white); white-space: nowrap; }
  .hero-title { font-size: 48px; font-weight: 600; line-height: 1.1; letter-spacing: 1px; }
  .hero-subtitle { font-size: 24px; font-weight: 600; margin-top: 2px; margin-left: 3px; }
  .hero-text { font-size: 14px; line-height: 21px; margin: 8px 0 0 3px; color: #eef2f4; white-space: normal; width: 490px; }
  .hero-actions { display: flex; gap: 11px; margin: 16px 0 0 3px; }
  .btn {
    display: inline-block; color: var(--white); text-decoration: none; font-size: 16px;
    height: 39px; line-height: 39px; padding: 0; border-radius: 2px; white-space: nowrap; text-align: center;
    box-shadow: 0 1px 3px rgba(0,0,0,0.35);
  }
  .btn-signup { background: linear-gradient(var(--btn-blue-top), var(--btn-blue-bottom)); width: 179px; }
  .btn-plans { background: linear-gradient(var(--btn-orange-top), var(--btn-orange-bottom)); width: 169px; }
  .slider-dots { position: absolute; left: 567px; top: 554px; display: flex; gap: 4px; }
  .slider-dots span { width: 14px; height: 14px; border-radius: 50%; background: var(--white); }
  .slider-dots span.active { background: #000; }

  .guides {
    position: absolute; left: 106px; top: 601px; width: 993px; height: 188px;
    background: var(--white); border: 1px solid var(--card-border);
    display: flex; padding: 19px 14px;
  }
  .guide { display: flex; width: 50%; }
  .guide + .guide { padding-left: 6px; }
  .guide-image { flex: none; width: 175px; height: 144px; border: 1px solid #d5dde0; }
  .guide-image.cloud { background: linear-gradient(135deg, #c8ccd0, #8c9298 55%, #6d7378); }
  .guide-image.browser { background: linear-gradient(160deg, #eaf6fc, #bfe1f3 50%, #8ec6e6); }
  .guide-body { padding-left: 12px; }
  .guide-title { font-size: 16px; font-weight: 600; color: var(--link); line-height: 22px; }
  .guide-text { font-size: 11px; line-height: 17.5px; color: var(--body-text); margin-top: 5px; }
  .guide-link { display: inline-block; margin-top: 8px; font-size: 12.5px; color: var(--link); text-decoration: none; white-space: nowrap; }

  .site-footer { position: absolute; left: 108px; top: 814px; width: 970px; height: 30px; }
  .copyright { font-size: 11.5px; color: var(--footer-text); line-height: 30px; white-space: nowrap; }
  .social { position: absolute; right: 0; top: 2px; display: flex; gap: 8px; }
  .social span { width: 24px; height: 24px; border-radius: 50%; background: var(--icon); display: block; }
</style>
</head>
<body>
<div class="page">
  <header class="site-header">
    <div class="header-inner">
      <div class="brand">
        <div class="brand-name">Pingo Qz</div>
        <div class="brand-slogan">Your Slogan goes here</div>
      </div>
      <nav class="main-nav">
        <a href="#">Home</a>
        <a href="#">How it Works</a>
        <a href="#">Support</a>
        <a href="#" class="login">Login</a>
      </nav>
    </div>
  </header>

  <section class="hero">
    <div class="hero-visual" role="img" aria-label="Photo of a hand touching an open white envelope with a green at-sign card"></div>
    <div class="hero-copy">
      <h1 class="hero-title">Duis tincidunt lectus</h1>
      <h2 class="hero-subtitle">Suspendisse vulputate aliquam</h2>
      <p class="hero-text">Duis tincidunt lectus quis dui viverra vestibulum. Suspendisse vulputate aliquam dui. Nulla elementum dui ut augue Aliquam</p>
      <div class="hero-actions">
        <a href="#" class="btn btn-signup">GET STARTED NOW</a>
        <a href="#" class="btn btn-plans">COMPARE PLANS</a>
      </div>
    </div>
  </section>
  <div class="slider-dots"><span class="active"></span><span></span><span></span><span></span></div>

  <section class="guides">
    <article class="guide">
      <div class="guide-image cloud" role="img" aria-label="Photo of a finger touching drawn cloud outlines"></div>
      <div class="guide-body">
        <h3 class="guide-title">How to Configure your skyveil DNS to use pingo.qz</h3>
        <p class="guide-text">Cum sociis natoque penatibus et magnis dis parturient montes nascetur ridiculus mus. In iaculis facilisis massa. Etiam eu urna. Sed porta. Suspendisse quam leo molestie sed luctusgiat</p>
        <a href="#" class="guide-link">Learn More &raquo;</a>
      </div>
    </article>
    <article class="guide">
      <div class="guide-image browser" role="img" aria-label="Illustration of a browser address bar with a globe and mouse pointer"></div>
      <div class="guide-body">
        <h3 class="guide-title">Use pingo.qz with your NameHarbor domain registration for reliable email forwarding</h3>
        <p class="guide-text">Cum sociis natoque penatibus et magnis dis parturient montes nascetur ridiculus mus. In iaculis facilisis massa. Etiam eu urna. Sed porta.</p>
        <a href="#" class="guide-link">Learn More &raquo;</a>
      </div>
    </article>
  </section>

  <footer class="site-footer">
    <p class="copyright">Copyright © 2014 Larkfield consulting. All Rights Reserved.</p>
    <div class="social">
      <span aria-label="Social profile 1"></span>
      <span aria-label="Social profile 2"></span>
      <span aria-label="Social profile 3"></span>
    </div>
  </footer>
</div>
</body>
</html>
```